KorvaNest - Home Income and Business Resources Platform

I am looking for a website template for a multi-purposed website. This website will feature:

1.) Website Directory with Ratings & comments on listings
2.) Company Blog
3.) Homepage with Content (see files for homepage mock)

I would like the Design to have a default width 1170px (wider then normal)

Of course I am looking for Pages for Listings to be designed.

Great looking BLOG Layout: http://journal.plimworks.example/html/blog.html

I would like 4 Versions of a Website Directory Listing "Box"
1.) Basic Listing Box
2.) Sponsored Listing Box
3.) Recommended Listing Box
4.) Stay Away From Listing Box

Information on the Listing Page (Like on a Category Page)
Site Name, Site URL, Website Image, # of Views, Rating and # of Comments

Information on the Listing Details Page:
Same as ABOVE + About website Description, Vornic Score, Category Information

Decent looking examples is here: https://samples.trevolin.example/directory/computers/ and http://www.zqrankhub.example/.

I will include some sketches and screenshots of things I like/looking for. As designers,you have creative freedom and are encouraged to show this. This is Phase one of this project and winning designer is guaranteed to have future work for this project.

Target Market(s)

Directory, business, websites

Industry/Entity Type

Business

Coding

Coded - Design and coding required

Number of Pages Required

5+ page

Font styles to use
Sans Serif

Colors

Designer to choose colors to be used in the design.

Requirements
Must have
• Professional yet clean look. The use of Icons & images
• Unique Look
Should not have
• Any exact copies of any examples I provided

```html
<!DOCTYPE html>
<html lang="en">
<head>
<meta charset="utf-8">
<title>KorvaNest</title>
<link href="https://fonts.googleapis.com/css2?family=Montserrat:wght@400;600;700&family=Open+Sans:wght@400;600;700&display=swap" rel="stylesheet">
<style>
:root{
  --red:#e2533f;
  --red-dark:#d6412f;
  --white:#ffffff;
  --ink:#222222;
  --blue:#3a78a0;
  --teal:#47b39a;
  --yellow:#efc64a;
  --orange:#e57b3d;
  --link:#2a8fcf;
  --line:#e3e3e3;
}
*{margin:0;padding:0;box-sizing:border-box}
html,body{width:1200px;height:928px;overflow:hidden;background:var(--white);font-family:"Open Sans",sans-serif}
.page{position:relative;width:1200px;height:928px}
.top-band{position:absolute;left:0;top:0;width:1200px;height:125px;background:linear-gradient(100deg,var(--red-dark),var(--red) 50%,#e0604c)}
.brand{position:absolute;left:60px;top:22px;color:var(--white);font:700 34px "Montserrat",sans-serif;letter-spacing:1px;white-space:nowrap}
.nav{position:absolute;left:354px;top:35px;display:flex;gap:32px;list-style:none}
.nav li{color:var(--white);font:600 12px "Montserrat",sans-serif;white-space:nowrap}
.login{position:absolute;left:1045px;top:24px;width:96px;height:36px;border-radius:10px;background:var(--white);color:var(--red);font:500 13px "Montserrat",sans-serif;display:flex;align-items:center;justify-content:center}
.sheet{position:absolute;left:60px;top:83px;width:1081px;height:740px;background:var(--white);border-radius:8px}
.footer{position:absolute;left:0;top:803px;width:1200px;height:125px;background:linear-gradient(100deg,var(--red-dark),var(--red) 50%,#e0604c)}
.copyright{position:absolute;top:34px;width:100%;text-align:center;color:var(--white);font:400 12px "Montserrat",sans-serif}
.social{position:absolute;top:66px;width:100%;display:flex;justify-content:center;gap:14px;list-style:none}
.social li{color:var(--white);font:600 12px "Open Sans",sans-serif;display:flex;align-items:center;gap:4px}
.social li::before{content:"";width:8px;height:8px;border-radius:50%;background:var(--white)}
.about{position:absolute;left:75px;top:102px;width:782px;height:213px;border-radius:8px;overflow:hidden;background:var(--blue)}
.about .photo{position:absolute;left:0;top:0;width:360px;height:213px;background:linear-gradient(135deg,#d9d3c6,#b7a58f 60%,#8d7a66);clip-path:polygon(0 0,100% 0,75% 100%,0 100%)}
.about h2{position:absolute;left:343px;top:36px;color:var(--white);font:700 17px "Open Sans",sans-serif;letter-spacing:.5px}
.about p{position:absolute;left:343px;top:68px;width:420px;color:var(--white);font:400 14px/23px "Open Sans",sans-serif}
.card{position:absolute;top:333px;width:250px;height:429px;border-radius:8px;overflow:hidden;box-shadow:0 3px 0 #d8d8d8}
.card .photo{height:184px}
.card .body{padding:22px 18px 0 18px;color:var(--white)}
.card .head{display:flex;align-items:center;gap:8px;height:42px;padding-bottom:14px;border-bottom:1px solid rgba(255,255,255,.35);box-sizing:content-box}
.card .head svg{flex:none}
.card h3{font:700 14px/19px "Open Sans",sans-serif;letter-spacing:.3px;white-space:nowrap}
.card p{margin-top:14px;font:400 13.5px/23px "Open Sans",sans-serif;opacity:.95}
.card .more{display:block;margin-top:16px;font:700 13px "Open Sans",sans-serif;letter-spacing:.5px}
.card-income{left:75px;background:var(--teal)}
.card-income .photo{background:linear-gradient(135deg,#3c3f44,#9b9a8f 55%,#d8c98a)}
.card-ads{left:341px;background:var(--yellow)}
.card-ads .photo{background:linear-gradient(135deg,#2b2d30,#9aa3ab 45%,#e9eef1)}
.card-earn{left:606px;background:var(--orange)}
.card-earn .photo{background:linear-gradient(135deg,#8fae4e,#c8a272 55%,#d6b25a)}
.sponsored{position:absolute;left:885px;top:103px;width:240px;height:413px;border:1px solid #ddd;border-radius:8px;box-shadow:0 3px 6px rgba(0,0,0,.12);background:var(--white);padding:20px}
.sponsored h2{font:700 16.5px "Open Sans",sans-serif;color:var(--ink);letter-spacing:.5px;margin-left:2px}
.listing{display:flex;align-items:center;height:92px;border-bottom:1px solid var(--line)}
.listing:last-child{border-bottom:none}
.listing .name{width:104px;flex:none;font:700 17px "Open Sans",sans-serif;color:var(--ink)}
.listing .desc{color:var(--link);font:400 14px/19px "Montserrat",sans-serif;white-space:nowrap}
.first{margin-top:12px;height:76px}
.ad{position:absolute;left:890px;top:532px;width:229px;height:230px;background:linear-gradient(110deg,#1f8a1f 0%,#2f9a2a 52%,#d9b58f 56%,#efe9e1 100%)}
</style>
</head>
<body>
<div class="page">
  <div class="top-band"></div>
  <div class="brand">KORVA NEST</div>
  <ul class="nav">
    <li>HOME</li><li>ABOUT US</li><li>RESOURCES</li><li>BENEFITS</li><li>EARNING</li><li>SPONSORS</li><li>CONTACT US</li>
  </ul>
  <div class="login">LOG IN</div>

  <div class="sheet"></div>

  <section class="about">
    <div class="photo" role="img" aria-label="Couple reviewing paperwork on a sofa"></div>
    <h2>ABOUT KORVANEST</h2>
    <p>Aliquam molestie, mi et imperdiet euismod, dui purus auctor tellus, et interdum lacus lectus et anteaccumsan sollicitudin sapien, sit amet adipiscing turpis gravida ac aliquam nibh a dui iaculis viverra id a velit. Vivamus egestas risus in magna varius commodo.</p>
  </section>

  <article class="card card-income">
    <div class="photo" role="img" aria-label="Person signing a document beside a small model house"></div>
    <div class="body">
      <div class="head">
        <svg width="32" height="40" viewBox="0 0 36 42"><path d="M2 1h22l10 10v30H2z" fill="#fff"/><path d="M24 1v10h10" fill="#d8f0ea"/><rect x="8" y="20" width="20" height="3" fill="#47b39a"/><rect x="8" y="26" width="20" height="3" fill="#47b39a"/><rect x="8" y="32" width="20" height="3" fill="#47b39a"/></svg>
        <h3>HOME INCOME<br>RESOURCE DIRECTORY</h3>
      </div>
      <p>Find what you need, when you need it.The KorvaNest website directory is your one-stop pit for anything involved...</p>
      <span class="more">LEARN MORE</span>
    </div>
  </article>

  <article class="card card-ads">
    <div class="photo" role="img" aria-label="Businessman holding a tablet showing an advertising diagram"></div>
    <div class="body">
      <div class="head">
        <svg width="52" height="34" viewBox="0 0 52 34"><rect x="8" y="2" width="36" height="24" rx="2" fill="none" stroke="#fff" stroke-width="3"/><rect x="1" y="28" width="50" height="4" rx="2" fill="#fff"/></svg>
        <h3>ADVERTISING<br>BENEFITS</h3>
      </div>
      <p>Everyone needs to advertise and we know just how to get your offer out to the right people. We have many methods...</p>
      <span class="more">LEARN MORE</span>
    </div>
  </article>

  <article class="card card-earn">
    <div class="photo" role="img" aria-label="Alarm clock beside growing stacks of coins with seedlings"></div>
    <div class="body">
      <div class="head">
        <svg width="30" height="48" viewBox="0 0 30 48"><text x="15" y="40" text-anchor="middle" font-family="Open Sans, sans-serif" font-weight="700" font-size="46" fill="#fff">$</text></svg>
        <h3>EARNING WITH<br>KORVANEST</h3>
      </div>
      <p>Join KorvaNest and start earning money. When you share KorvaNest and lock in an advertiser or premium listing,</p>
      <span class="more">LEARN MORE</span>
    </div>
  </article>

  <aside class="sponsored">
    <h2>SPONSORED LISTING</h2>
    <div class="listing first"><span class="name">Ordwell</span><span class="desc">Lorem ipsum<br>dolor sit..</span></div>
    <div class="listing"><span class="name">Tamsfield</span><span class="desc">Lorem ipsum<br>dolor sit..</span></div>
    <div class="listing"><span class="name">Lumarc</span><span class="desc">Lorem ipsum<br>dolor sit..</span></div>
    <div class="listing"><span class="name">Pennrow</span><span class="desc">Lorem ipsum<br>dolor sit..</span></div>
  </aside>

  <div class="ad" role="img" aria-label="Advertisement banner inviting visitors to take paid surveys, with a woman working at a laptop"></div>

  <footer class="footer">
    <p class="copyright">Copyrigit © 2017. Company Name. All Right Reserved</p>
    <ul class="social">
      <li>Zunto</li><li>Quillo</li><li>Gravel</li><li>Pixmo</li><li>Merrow</li><li>Vidlo</li>
    </ul>
  </footer>
</div>
</body>
</html>
```